I need a business card design for a real estate finance, development and management business. We deal with high net worth clients and ask that the business card be neat, clean and sophisticated. We like the attached logo design, font and color and want to incorporate all this into the business card.

Industry/Entity Type

Real Estate

```html
<!DOCTYPE html>
<html lang="en">
<head>
<meta charset="utf-8">
<title>Silver Harbor – Business Card</title>
<link href="https://fonts.googleapis.com/css2?family=Open+Sans:wght@400;600;700&display=swap" rel="stylesheet">
<style>
  :root {
    --brand-blue: #1f5c9e;
    --panel-grey: #dcdcdc;
    --card-white: #ffffff;
    --ink: #1e1e1e;
    --backdrop: #e6e6e6;
  }
  * { box-sizing: border-box; margin: 0; padding: 0; }
  html, body { width: 1200px; height: 947px; overflow: hidden; }
  body {
    background: var(--backdrop);
    font-family: "Open Sans", Arial, sans-serif;
    position: relative;
  }
  .card {
    position: absolute;
    width: 560px;
    height: 320px;
    background: var(--card-white);
    box-shadow: 0 6px 18px rgba(0,0,0,0.12);
  }

  /* Back of card */
  .card-back {
    left: 580px;
    top: 110px;
    border: 16px solid var(--brand-blue);
    display: flex;
    align-items: center;
    justify-content: center;
  }
  .wordmark {
    font-family: "Open Sans", Arial, sans-serif;
    font-weight: 600;
    color: var(--brand-blue);
    text-transform: uppercase;
    letter-spacing: 0.08em;
    display: flex;
    align-items: center;
    gap: 12px;
  }
  .card-back .wordmark { font-size: 40px; }
  .wordmark-square {
    width: 12px; height: 12px;
    background: var(--brand-blue);
  }

  /* Front of card */
  .card-front { left: 60px; top: 500px; }
  .top-rule {
    position: absolute; left: 18px; right: 18px; top: 22px;
    height: 2px; background: var(--brand-blue);
  }
  .card-front .wordmark {
    position: absolute; right: 40px; top: 58px; font-size: 27px;
  }
  .mobile-line {
    position: absolute; left: 18px; top: 58px;
    display: flex; align-items: center; gap: 10px;
    color: var(--brand-blue); font-size: 15px;
  }
  .frame-rule {
    position: absolute; left: 18px; top: 122px; width: 340px;
    height: 1px; background: var(--brand-blue);
  }
  .frame-side {
    position: absolute; left: 18px; top: 58px; width: 1px; height: 64px;
    background: var(--brand-blue);
  }
  .name-band {
    position: absolute; left: 358px; top: 122px; width: 184px; height: 38px;
    background: var(--brand-blue); color: var(--card-white);
    font-size: 18px; letter-spacing: 0.04em;
    display: flex; align-items: center; justify-content: center;
  }
  .name-band strong { font-weight: 700; }
  .info-row {
    position: absolute; left: 18px; right: 18px; top: 134px; bottom: 16px;
    display: grid; grid-template-columns: 1fr 1fr 1fr; gap: 10px;
  }
  .info-panel {
    background: var(--panel-grey);
    border-radius: 12px;
    display: flex; flex-direction: column; align-items: center; justify-content: center;
    gap: 6px; color: var(--ink); font-size: 14px; line-height: 1.3; text-align: center;
  }
  .info-panel.contact-online { margin-top: 38px; }
  .info-panel svg { fill: var(--ink); }
</style>
</head>
<body>

  <section class="card card-back" aria-label="Card back">
    <div class="wordmark"><span class="wordmark-square"></span>Silver Harbor</div>
  </section>

  <section class="card card-front" aria-label="Card front">
    <div class="top-rule"></div>
    <div class="frame-side"></div>
    <div class="mobile-line">
      <svg width="22" height="30" viewBox="0 0 22 30" aria-hidden="true">
        <rect x="1.5" y="1.5" width="19" height="27" rx="3" fill="none" stroke="currentColor" stroke-width="2.5"/>
        <rect x="5" y="5" width="12" height="17" fill="currentColor"/>
        <circle cx="11" cy="25" r="1.4" fill="currentColor"/>
      </svg>
      <span>+0000 1234 5679</span>
    </div>
    <div class="wordmark"><span class="wordmark-square"></span>Silver Harbor</div>
    <div class="frame-rule"></div>
    <div class="name-band">YOUR<strong>NAME</strong></div>

    <div class="info-row">
      <div class="info-panel contact-address">
        <svg width="16" height="14" viewBox="0 0 16 14" aria-hidden="true">
          <path d="M8 0 L16 7 H13.5 V14 H9.5 V10 H6.5 V14 H2.5 V7 H0 Z"/>
        </svg>
        <span>Your Local or<br>business address.</span>
      </div>
      <div class="info-panel contact-phone">
        <svg width="18" height="14" viewBox="0 0 18 14" aria-hidden="true">
          <path d="M1 4 C1 1 17 1 17 4 V6 H13 V4 H5 V6 H1 Z"/>
          <path d="M4 7 H14 L16 13 H2 Z"/>
        </svg>
        <span>+000 1234 5679<br>+000 1234 5679</span>
      </div>
      <div class="info-panel contact-online">
        <svg width="18" height="14" viewBox="0 0 18 14" aria-hidden="true">
          <rect x="0" y="0" width="18" height="11"/>
          <rect x="6" y="12" width="6" height="2"/>
        </svg>
        <span>name@yourwebsite.com<br>www.yourwebsite.com</span>
      </div>
    </div>
  </section>

</body>
</html>
```